School Poster

Design so that these can be placed in classrooms across the school.

Attached is another design we have had done. Use a similar theme.

Consider using themes from https://corvalhs.edq.example.au/

please edit Binder1 doc.

Students and teachers

```html
<!DOCTYPE html>
<html lang="en">
<head>
<meta charset="utf-8">
<title>Corval SHS – Classroom Posters</title>
<link rel="stylesheet" href="https://fonts.googleapis.com/css2?family=Poppins:wght@300;400;500;600;700;800;900&display=swap">
<style>
:root{
  --blue:#2e4a94;
  --yellow:#f4e45a;
  --ink:#2a2a2a;
  --red:#d42a2a;
  --stage:#888a89;
  --mist:#eeeeef;
  --white:#ffffff;
}
*{box-sizing:border-box;margin:0;padding:0}
html,body{width:1200px;height:960px;overflow:hidden}
body{background:var(--stage);font-family:"Poppins",sans-serif;color:var(--ink);position:relative}
.poster{position:absolute;top:144px;width:476px;height:672px;background:var(--white);overflow:hidden}
.poster--ask{left:106px}
.poster--ai{left:618px}
.header{position:absolute;left:0;top:0;width:100%;height:145px;background:var(--blue)}
.title{position:absolute;left:24px;color:var(--white);font-weight:800;font-size:33px;line-height:32px;letter-spacing:.3px}
.brand{position:absolute;right:22px;top:22px;display:flex;align-items:center;gap:6px;color:var(--white);font-weight:700;font-size:14px;letter-spacing:.5px}
.brand__dot{width:12px;height:12px;border-radius:50%;background:var(--yellow)}
/* left poster */
.poster--ask .title{top:23px}
.subtitle-band{position:absolute;left:0;top:92px;width:100%;height:28px;background:var(--yellow)}
.subtitle{position:absolute;left:24px;top:-2px;font-size:24px;font-weight:400;color:var(--ink);letter-spacing:.3px;line-height:32px}
.step{position:absolute;top:168px;width:136px;height:414px;border:2px solid var(--blue);border-radius:9px;background:var(--white)}
.step--1{left:24px}.step--2{left:170px}.step--3{left:315px}
.step__num{position:absolute;left:50%;top:-14px;transform:translateX(-50%);width:27px;height:27px;border-radius:50%;background:var(--blue);color:var(--white);font-weight:700;font-size:16px;line-height:27px;text-align:center;box-shadow:0 0 0 6px var(--white)}
.step__icon{position:absolute;left:28px;top:24px;width:78px;height:86px;border-radius:12px;background:linear-gradient(160deg,var(--yellow),var(--blue))}
.step__title{position:absolute;left:0;width:100%;text-align:center;color:var(--blue);font-weight:800;font-size:19.5px;line-height:19px;text-transform:uppercase}
.step__lead{position:absolute;left:0;top:194px;width:100%;height:45px;background:var(--yellow);display:flex;align-items:center;justify-content:center;text-align:center;font-weight:700;font-size:12.2px;line-height:13px;padding:0 4px}
.step__body{position:absolute;left:0;top:239px;width:100%;height:173px;background:var(--mist);border-radius:0 0 7px 7px;padding:7px 4px 0 10px}
.step__body ul{list-style:none}
.step__body li{position:relative;padding-left:12px;font-size:9.8px;line-height:13.8px;margin-bottom:3px;letter-spacing:-.1px}
.step__body li::before{content:"";position:absolute;left:0;top:5px;width:4px;height:4px;border-radius:50%;background:var(--ink)}
.step--2 .step__body li::before{background:var(--blue)}
.step__note{font-weight:700;font-size:9.8px;line-height:13.8px;margin-top:1px;letter-spacing:-.1px}
.step__motto{position:absolute;left:50%;bottom:-14px;transform:translateX(-50%);width:113px;height:26px;border-radius:8px;background:var(--blue);color:var(--white);font-weight:800;font-size:15.5px;line-height:26px;text-align:center;white-space:nowrap;box-shadow:0 0 0 3px var(--white)}
.references{position:absolute;left:0;top:607px;width:100%;height:65px;background:var(--yellow);padding:8px 20px 0 54px;font-size:6.6px;line-height:8.4px;color:#3a3a3a}
.references strong{display:block;font-weight:700;margin-bottom:2px}
/* right poster */
.poster--ai .title{top:48px}
.accent-stripe{position:absolute;left:0;top:112px;width:100%;height:9px;background:var(--yellow)}
.lower-wash{position:absolute;left:0;top:347px;width:100%;height:295px;background:var(--mist)}
.heading{position:absolute;left:0;width:100%;text-align:center;color:var(--blue);font-weight:800;font-size:20px;line-height:22px}
.must-list{position:absolute;list-style:none;font-weight:700;font-size:11.6px;line-height:14.6px}
.must-list li{position:relative;padding-left:15px;margin-bottom:3.5px}
.must-list svg{position:absolute;left:0;top:3px}
.must-list--a{left:32px;top:183px;width:200px}
.must-list--b{left:244px;top:183px;width:200px}
.help-box{position:absolute;left:24px;top:269px;width:427px;height:206px;background:var(--yellow);border-radius:8px}
.help-box .heading{top:10px}
.help-note{position:absolute;left:0;top:31px;width:100%;text-align:center;font-size:12.5px;color:var(--blue);font-weight:400}
.grid{position:absolute;left:0;width:100%;display:flex}
.grid__item{flex:1;position:relative;text-align:center;font-weight:700;font-size:11.8px;line-height:13px}
.grid__item + .grid__item{border-left:1px solid #8a8a70}
.help-grid{top:66px;height:124px}
.help-grid .grid__item{padding:0 6px}
.help-icon{width:62px;height:64px;margin:-4px auto 10px;border-radius:12px;background:linear-gradient(160deg,var(--blue),#5a72b4)}
.cannot-grid .grid__item{border-color:#c9c9c9;padding:0 5px}
.cross{display:block;margin:3px auto 10px}
.footer-line{position:absolute;left:0;top:642px;width:100%;height:30px;background:var(--blue);color:var(--white);font-weight:700;font-size:11.6px;line-height:30px;text-align:center}
</style>
</head>
<body>

<section class="poster poster--ask" aria-label="Before you ask the teacher poster">
  <div class="header">
    <h1 class="title">BEFORE YOU ASK<br>THE TEACHER...</h1>
    <div class="brand"><span class="brand__dot"></span>CORVAL SHS</div>
  </div>
  <div class="subtitle-band"><p class="subtitle">TRY THESE STEPS FIRST!</p></div>

  <article class="step step--1">
    <span class="step__num">1</span>
    <div class="step__icon" role="img" aria-label="Icon of a head in profile with a lightbulb"></div>
    <h2 class="step__title" style="top:134px">Think<br>First</h2>
    <p class="step__lead">Don't give up<br>straight away.</p>
    <div class="step__body">
      <ul>
        <li>Read the question carefully.</li>
        <li>Identify what you already know.</li>
        <li>Try a strategy you've used before.</li>
        <li>Give yourself thinking time.</li>
      </ul>
    </div>
    <span class="step__motto">WE BELIEVE</span>
  </article>

  <article class="step step--2">
    <span class="step__num">2</span>
    <div class="step__icon" role="img" aria-label="Icon of a clipboard checklist"></div>
    <h2 class="step__title" style="top:123px">Check<br>Your<br>Supports</h2>
    <p class="step__lead">Before asking for<br>help, check:</p>
    <div class="step__body">
      <ul>
        <li>Learning goal and success criteria.</li>
        <li>Worked examples.</li>
        <li>Class notes.</li>
        <li>Classroom displays.</li>
        <li>EdPath resources.</li>
        <li>Task sheet and instructions.</li>
      </ul>
    </div>
    <span class="step__motto">WE STRIVE</span>
  </article>

  <article class="step step--3">
    <span class="step__num">3</span>
    <div class="step__icon" role="img" aria-label="Icon of three people with speech bubbles"></div>
    <h2 class="step__title" style="top:134px">Ask 3<br>Before Me</h2>
    <p class="step__lead">Ask three sources before asking the teacher:</p>
    <div class="step__body">
      <ul>
        <li>A person (partner or neighbour)</li>
        <li>A place (notes, display, EdPath)</li>
        <li>A resource (worked example, task sheet)</li>
      </ul>
      <p class="step__note">Then ask the teacher if you still need help.</p>
    </div>
    <span class="step__motto">WE ACHIEVE</span>
  </article>

  <footer class="references">
    <strong>References</strong>
    Harwood, L. (2025). Why Students Don't Ask for Help – And How to Change That. Downloaded 24/04/2026 from:https://www.learnwell.example.org/article/asking-for-help/<br>
    ELRO. (2024). Supporting Self-Regulated Learning. Downloaded 24/04/2026 from:https://www.evidencehub.example.au/files/2024-02/self-regulated-learning-guide.pdf
  </footer>
</section>

<section class="poster poster--ai" aria-label="Using AI responsibly poster">
  <div class="header">
    <h1 class="title">USING AI AND OTHER<br>TOOLS RESPONSIBLY</h1>
    <div class="accent-stripe"></div>
    <div class="brand"><span class="brand__dot"></span>CORVAL SHS</div>
  </div>
  <div class="lower-wash"></div>

  <h2 class="heading" style="top:153px">WHAT YOU MUST DO:</h2>
  <ul class="must-list must-list--a">
    <li><svg width="8" height="8" viewBox="0 0 8 8"><rect x=".5" y=".5" width="7" height="7" fill="none" stroke="#2e4a94"/><path d="M1.8 4l1.5 1.5L6.3 2" fill="none" stroke="#2e4a94" stroke-width="1.1"/></svg>Complete your own work</li>
    <li><svg width="8" height="8" viewBox="0 0 8 8"><rect x=".5" y=".5" width="7" height="7" fill="none" stroke="#2e4a94"/><path d="M1.8 4l1.5 1.5L6.3 2" fill="none" stroke="#2e4a94" stroke-width="1.1"/></svg>Demonstrate your progress (drafts, notes, planning, revisions)</li>
  </ul>
  <ul class="must-list must-list--b">
    <li><svg width="8" height="8" viewBox="0 0 8 8"><rect x=".5" y=".5" width="7" height="7" fill="none" stroke="#2e4a94"/><path d="M1.8 4l1.5 1.5L6.3 2" fill="none" stroke="#2e4a94" stroke-width="1.1"/></svg>Use feedback to improve your work</li>
    <li><svg width="8" height="8" viewBox="0 0 8 8"><rect x=".5" y=".5" width="7" height="7" fill="none" stroke="#2e4a94"/><path d="M1.8 4l1.5 1.5L6.3 2" fill="none" stroke="#2e4a94" stroke-width="1.1"/></svg>Demonstrate your understanding of the ideas in your submission</li>
  </ul>

  <div class="help-box">
    <h2 class="heading">WHAT AI CAN HELP YOU DO</h2>
    <p class="help-note">(when approved by your teacher)</p>
    <div class="grid help-grid">
      <div class="grid__item"><div class="help-icon" role="img" aria-label="Icon of a brain"></div>Brainstorm<br>ideas</div>
      <div class="grid__item"><div class="help-icon" role="img" aria-label="Icon of a checklist with magnifier"></div>Check spelling, grammar and clarity</div>
      <div class="grid__item"><div class="help-icon" role="img" aria-label="Icon of a phone reading text aloud"></div>Read your work aloud using text-to-speech tools</div>
      <div class="grid__item"><div class="help-icon" role="img" aria-label="Icon of a rising bar chart with gear"></div>Help identify areas for improvement in a draft</div>
    </div>
  </div>

  <h2 class="heading" style="top:488px">WHAT YOU CANNOT DO:</h2>
  <div class="grid cannot-grid" style="left:0;width:476px;padding:0 24px;top:513px;height:120px">
    <div class="grid__item"><svg class="cross" width="36" height="36" viewBox="0 0 36 36"><circle cx="18" cy="18" r="15.5" fill="none" stroke="#d42a2a" stroke-width="3"/><path d="M12 12l12 12M24 12L12 24" stroke="#d42a2a" stroke-width="3" stroke-linecap="round"/></svg>Submit AI-generated work as your own</div>
    <div class="grid__item"><svg class="cross" width="36" height="36" viewBox="0 0 36 36"><circle cx="18" cy="18" r="15.5" fill="none" stroke="#d42a2a" stroke-width="3"/><path d="M12 12l12 12M24 12L12 24" stroke="#d42a2a" stroke-width="3" stroke-linecap="round"/></svg>Copy and paste AI responses without acknowledging or adapting them</div>
    <div class="grid__item"><svg class="cross" width="36" height="36" viewBox="0 0 36 36"><circle cx="18" cy="18" r="15.5" fill="none" stroke="#d42a2a" stroke-width="3"/><path d="M12 12l12 12M24 12L12 24" stroke="#d42a2a" stroke-width="3" stroke-linecap="round"/></svg>Use AI tools to complete the whole task for you</div>
    <div class="grid__item"><svg class="cross" width="36" height="36" viewBox="0 0 36 36"><circle cx="18" cy="18" r="15.5" fill="none" stroke="#d42a2a" stroke-width="3"/><path d="M12 12l12 12M24 12L12 24" stroke="#d42a2a" stroke-width="3" stroke-linecap="round"/></svg>Submit work that does not demonstrate your understanding</div>
  </div>

  <footer class="footer-line">If you didn't create, develop and understand it, it isn't your work.</footer>
</section>

</body>
</html>
```